1/4 & 1/2 Page Ad For Marketing

Looking to have a ad that we can use for various community advertising requests. We are a wholesale / retail center of landscape supplies. I have attached an aerial photo of our yard some past ad content as well as our new logo designs which is the one with 6 logos which anyone can be used. Would like to be able to use in full color but also black and white.

Industry/Entity Type

Wholesale Retail of Landscape Supplies

Font styles to use
Sans Serif

Colors
59FF00
82FF00
B8FF75
E3FFCB
F4FFEA

Requirements
Must have
• Birch Hollow Yard has a wide variety of decorative stone, mulch, gravel, topsoil and sand products for all your landscaping needs. 920-555-0147 www.birchhollowyardllc.example

```html
<!DOCTYPE html>
<html lang="en">
<head>
<meta charset="utf-8">
<title>Birch Hollow Yard – Half and Quarter Page Ads</title>
<link href="https://fonts.googleapis.com/css2?family=League+Spartan:wght@600;700;800&family=Oswald:wght@500&family=Arimo&display=swap" rel="stylesheet">
<style>
  :root{
    --stage:#b1b1b1;
    --label:#eeeeee;
    --green:#6cc24a;
    --green-bright:#5cc12a;
    --ink:#1f1f1f;
    --white:#ffffff;
  }
  *{margin:0;padding:0;box-sizing:border-box}
  html,body{width:832px;height:1200px;overflow:hidden;background:var(--stage)}
  .canvas{position:relative;width:832px;height:1200px}

  .ad{position:absolute;overflow:hidden;background:var(--green);font-family:"League Spartan",sans-serif;color:var(--ink)}
  .ad--half{left:195px;top:46px;width:429px;height:555px}
  .ad--quarter{left:132px;top:680px;width:555px;height:428px}
  .ad__art{position:absolute;inset:0;width:100%;height:100%}

  .brand{position:absolute;display:flex;flex-direction:column;align-items:center;gap:3px;transform:translate(-50%,-50%);text-align:center;font-weight:800;line-height:1;color:var(--ink)}
  .brand__dot{width:12px;height:12px;border-radius:50%;background:var(--ink)}
  .ad--half .brand{left:63px;top:82px;font-size:11px}
  .ad--quarter .brand{left:209px;top:39px;font-size:12px}

  .headline{position:absolute;font-weight:800;text-transform:uppercase;white-space:nowrap}
  .headline__intro{display:block;color:var(--white)}
  .headline__lead{display:block;color:var(--ink)}
  .headline__main{display:block;color:var(--ink)}
  .ad--half .headline{left:27px;top:137px}
  .ad--half .headline__intro,.ad--half .headline__lead{font-size:18px;line-height:24px}
  .ad--half .headline__main{font-size:30px;line-height:32px}
  .ad--quarter .headline{left:35px;top:43.5px}
  .ad--quarter .headline__intro,.ad--quarter .headline__lead{font-size:22px;line-height:29px}
  .ad--quarter .headline__main{font-size:36px;line-height:39px}

  .offer-box{position:absolute;border:1.5px solid var(--ink);border-bottom:none;font-weight:700;text-transform:uppercase}
  .offer-box__list{list-style:none}
  .offer-box__item{display:flex;align-items:center;white-space:nowrap}
  .offer-box__tick{display:inline-flex;align-items:center}
  .offer-box__tick svg{display:block}
  .offer-box__foot{position:absolute;left:0;right:0;bottom:0;display:flex;align-items:center;white-space:nowrap}
  .offer-box__foot::before,.offer-box__foot::after{content:"";height:1.5px;background:var(--ink)}
  .offer-box__foot::before{margin-left:-1.5px}
  .offer-box__foot::after{flex:1;margin-right:-1.5px}

  .ad--half .offer-box{left:25px;top:280px;width:210px;height:57px;font-size:9px}
  .ad--half .offer-box__list{padding:5px 0 0 10px}
  .ad--half .offer-box__item{height:14px;gap:4px}
  .ad--half .offer-box__foot{transform:translateY(50%)}
  .ad--half .offer-box__foot::before{width:19px;margin-right:4px}
  .ad--half .offer-box__foot::after{margin-left:4px}

  .ad--quarter .offer-box{left:34px;top:220px;width:273px;height:75px;font-size:11.5px}
  .ad--quarter .offer-box__list{padding:7px 0 0 14px}
  .ad--quarter .offer-box__item{height:18.5px;gap:6px}
  .ad--quarter .offer-box__foot{transform:translateY(50%)}
  .ad--quarter .offer-box__foot::before{width:24px;margin-right:6px}
  .ad--quarter .offer-box__foot::after{margin-left:6px}

  .item-group{display:inline-flex;align-items:center;gap:4px;margin-right:8px}

  .service{position:absolute;font-family:"Oswald",sans-serif;font-weight:500;text-transform:uppercase;color:var(--ink);white-space:nowrap}
  .service__accent{color:var(--green-bright)}
  .ad--half .service{left:29px;top:360px;font-size:15px;line-height:21px}
  .ad--quarter .service{left:38px;top:322px;font-size:19px;line-height:24px}

  .contact-bar{position:absolute;left:0;right:0;bottom:0;display:flex;align-items:center;justify-content:center;background:var(--ink);color:var(--white);font-weight:700;white-space:nowrap}
  .contact-bar__item{display:inline-flex;align-items:center;gap:5px}
  .contact-bar__sep{display:inline-block;width:1.5px;background:var(--white)}
  .ad--half .contact-bar{height:31px;font-size:14.5px;gap:10px}
  .ad--half .contact-bar__sep{height:14px}
  .ad--quarter .contact-bar{height:32px;font-size:16px;gap:14px}
  .ad--quarter .contact-bar__sep{height:16px}

  .size-label{position:absolute;left:0;width:832px;text-align:center;font-family:"Arimo",sans-serif;font-size:31px;color:var(--label);line-height:1}
  .size-label--half{top:619px}
  .size-label--quarter{top:1137px}
</style>
</head>
<body>
<div class="canvas">

  <!-- Half page ad -->
  <section class="ad ad--half">
    <svg class="ad__art" viewBox="374 88 823 1065" preserveAspectRatio="none" aria-hidden="false">
      <defs>
        <linearGradient id="half-band" x1="0" x2="1"><stop offset="0" stop-color="#fff" stop-opacity=".95"/><stop offset=".75" stop-color="#fff" stop-opacity=".85"/><stop offset="1" stop-color="#fff" stop-opacity="0"/></linearGradient>
        <linearGradient id="half-yard" x1="0" y1="0" x2="1" y2="1"><stop offset="0" stop-color="#6f9a4a"/><stop offset="1" stop-color="#cfc6b6"/></linearGradient>
        <linearGradient id="half-truck" x1="0" y1="0" x2="1" y2="1"><stop offset="0" stop-color="#7b8a62"/><stop offset=".5" stop-color="#b3916a"/><stop offset="1" stop-color="#c8b8a0"/></linearGradient>
      </defs>
      <polygon fill="#ffffff" points="765,88 798,88 640,246 640,274 990,630 958,632 605,274 605,246"/>
      <polygon fill="#1f1f1f" points="798,88 1197,88 1197,1093 1100,1093 640,274 640,246"/>
      <g role="img" aria-label="Photo of grey crushed gravel"><rect x="710" y="165" width="191" height="191" rx="22" fill="#85898d" transform="rotate(45 805 260)"/></g>
      <g role="img" aria-label="Photo of pink crushed stone"><rect x="875" y="55" width="191" height="191" rx="22" fill="#b79491" transform="rotate(45 970 150)"/></g>
      <g role="img" aria-label="Photo of tan decorative stone"><rect x="1015" y="175" width="191" height="191" rx="22" fill="#b48a5a" transform="rotate(45 1110 270)"/></g>
      <g role="img" aria-label="Photo of landscape boulders"><rect x="875" y="335" width="191" height="191" rx="22" fill="#9b8e82" transform="rotate(45 970 430)"/></g>
      <g role="img" aria-label="Photo of mixed colour rock"><rect x="1015" y="500" width="191" height="191" rx="22" fill="#80818a" transform="rotate(45 1110 595)"/></g>
      <rect x="374" y="860" width="400" height="233" fill="url(#half-yard)" role="img" aria-label="Aerial photo of the supply yard"/>
      <polygon fill="url(#half-truck)" points="980,640 1197,855 1197,1093 690,1093" role="img" aria-label="Photo of the green delivery truck beside mulch piles"/>
      <rect x="374" y="765" width="500" height="97" fill="url(#half-band)"/>
    </svg>

    <div class="brand"><span class="brand__dot"></span><span>BIRCH HOLLOW<br>YARD</span></div>

    <h1 class="headline">
      <span class="headline__intro">We are a</span>
      <span class="headline__intro">Wholesale &amp;</span>
      <span class="headline__lead">Retail center of</span>
      <span class="headline__main">Landscape</span>
      <span class="headline__main">Supplies</span>
    </h1>

    <div class="offer-box">
      <ul class="offer-box__list">
        <li class="offer-box__item"><span class="item-group"><span class="offer-box__tick"><svg width="8" height="7" viewBox="0 0 10 8"><path d="M1 4l3 3 5-6" fill="none" stroke="#1f1f1f" stroke-width="1.8"/></svg></span>Decorative stone</span></li>
        <li class="offer-box__item"><span class="item-group"><span class="offer-box__tick"><svg width="8" height="7" viewBox="0 0 10 8"><path d="M1 4l3 3 5-6" fill="none" stroke="#1f1f1f" stroke-width="1.8"/></svg></span>Mulch</span><span class="item-group"><span class="offer-box__tick"><svg width="8" height="7" viewBox="0 0 10 8"><path d="M1 4l3 3 5-6" fill="none" stroke="#1f1f1f" stroke-width="1.8"/></svg></span>Gravel</span><span class="item-group"><span class="offer-box__tick"><svg width="8" height="7" viewBox="0 0 10 8"><path d="M1 4l3 3 5-6" fill="none" stroke="#1f1f1f" stroke-width="1.8"/></svg></span>Topsoil</span></li>
        <li class="offer-box__item"><span class="item-group"><span class="offer-box__tick"><svg width="8" height="7" viewBox="0 0 10 8"><path d="M1 4l3 3 5-6" fill="none" stroke="#1f1f1f" stroke-width="1.8"/></svg></span>Sand products</span></li>
      </ul>
      <div class="offer-box__foot">For all your landscaping needs</div>
    </div>

    <p class="service">Over <span class="service__accent">20 varieties</span> of stone<br>Pick-up &amp; delivery available</p>

    <footer class="contact-bar">
      <span class="contact-bar__item"><svg width="12" height="12" viewBox="0 0 24 24"><path d="M6.6 10.8a15 15 0 0 0 6.6 6.6l2.2-2.2a1 1 0 0 1 1-.25 11.4 11.4 0 0 0 3.6.6 1 1 0 0 1 1 1V20a1 1 0 0 1-1 1A17 17 0 0 1 3 4a1 1 0 0 1 1-1h3.5a1 1 0 0 1 1 1 11.4 11.4 0 0 0 .6 3.6 1 1 0 0 1-.25 1z" fill="#fff"/></svg>920-555-0147</span>
      <span class="contact-bar__sep"></span>
      <span class="contact-bar__item"><svg width="11" height="11" viewBox="0 0 24 24"><g fill="none" stroke="#fff" stroke-width="2"><circle cx="12" cy="12" r="10"/><ellipse cx="12" cy="12" rx="4" ry="10"/><path d="M2 12h20"/></g></svg>www.birchhollowyardllc.example</span>
    </footer>
  </section>
  <p class="size-label size-label--half">1/2 page ad</p>

  <!-- Quarter page ad -->
  <section class="ad ad--quarter">
    <svg class="ad__art" viewBox="253 1305 1065 821" preserveAspectRatio="none">
      <defs>
        <linearGradient id="quarter-band" x1="0" x2="1"><stop offset="0" stop-color="#fff" stop-opacity=".95"/><stop offset=".7" stop-color="#fff" stop-opacity=".85"/><stop offset="1" stop-color="#fff" stop-opacity="0"/></linearGradient>
        <linearGradient id="quarter-yard" x1="0" x2="1"><stop offset="0" stop-color="#6f9a4a"/><stop offset="1" stop-color="#a9bf8d"/></linearGradient>
        <linearGradient id="quarter-truck" x1="0" y1="0" x2="1" y2="1"><stop offset="0" stop-color="#7b8a62"/><stop offset=".5" stop-color="#b3916a"/><stop offset="1" stop-color="#c8b8a0"/></linearGradient>
      </defs>
      <polygon fill="#ffffff" points="878,1305 908,1305 760,1452 760,1480 1110,1828 1080,1830 735,1480 735,1452"/>
      <polygon fill="#1f1f1f" points="908,1305 1318,1305 1318,2126 1250,2126 760,1480 760,1452"/>
      <g role="img" aria-label="Photo of grey crushed gravel"><rect x="840" y="1370" width="191" height="191" rx="22" fill="#85898d" transform="rotate(45 935 1465)"/></g>
      <g role="img" aria-label="Photo of pink crushed stone"><rect x="1005" y="1265" width="191" height="191" rx="22" fill="#b79491" transform="rotate(45 1100 1360)"/></g>
      <g role="img" aria-label="Photo of tan decorative stone"><rect x="1135" y="1380" width="191" height="191" rx="22" fill="#b48a5a" transform="rotate(45 1230 1475)"/></g>
      <g role="img" aria-label="Photo of landscape boulders"><rect x="1005" y="1545" width="191" height="191" rx="22" fill="#9b8e82" transform="rotate(45 1100 1640)"/></g>
      <g role="img" aria-label="Photo of mixed colour rock"><rect x="1135" y="1705" width="191" height="191" rx="22" fill="#80818a" transform="rotate(45 1230 1800)"/></g>
      <rect x="253" y="2015" width="700" height="52" fill="url(#quarter-yard)" role="img" aria-label="Aerial photo of the supply yard"/>
      <polygon fill="url(#quarter-truck)" points="1105,1830 1318,2045 1318,2067 870,2067" role="img" aria-label="Photo of the green delivery truck beside mulch piles"/>
      <rect x="253" y="1905" width="740" height="112" fill="url(#quarter-band)"/>
    </svg>

    <div class="brand"><span class="brand__dot"></span><span>BIRCH HOLLOW<br>YARD</span></div>

    <h2 class="headline">
      <span class="headline__intro">We are a</span>
      <span class="headline__intro">Wholesale &amp;</span>
      <span class="headline__lead">Retail center of</span>
      <span class="headline__main">Landscape</span>
      <span class="headline__main">Supplies</span>
    </h2>

    <div class="offer-box">
      <ul class="offer-box__list">
        <li class="offer-box__item"><span class="item-group"><span class="offer-box__tick"><svg width="10" height="8" viewBox="0 0 10 8"><path d="M1 4l3 3 5-6" fill="none" stroke="#1f1f1f" stroke-width="1.8"/></svg></span>Decorative stone</span></li>
        <li class="offer-box__item"><span class="item-group"><span class="offer-box__tick"><svg width="10" height="8" viewBox="0 0 10 8"><path d="M1 4l3 3 5-6" fill="none" stroke="#1f1f1f" stroke-width="1.8"/></svg></span>Mulch</span><span class="item-group"><span class="offer-box__tick"><svg width="10" height="8" viewBox="0 0 10 8"><path d="M1 4l3 3 5-6" fill="none" stroke="#1f1f1f" stroke-width="1.8"/></svg></span>Gravel</span><span class="item-group"><span class="offer-box__tick"><svg width="10" height="8" viewBox="0 0 10 8"><path d="M1 4l3 3 5-6" fill="none" stroke="#1f1f1f" stroke-width="1.8"/></svg></span>Topsoil</span></li>
        <li class="offer-box__item"><span class="item-group"><span class="offer-box__tick"><svg width="10" height="8" viewBox="0 0 10 8"><path d="M1 4l3 3 5-6" fill="none" stroke="#1f1f1f" stroke-width="1.8"/></svg></span>Sand products</span></li>
      </ul>
      <div class="offer-box__foot">For all your landscaping needs</div>
    </div>

    <p class="service">Over <span class="service__accent">20 varieties</span> of stone<br>Pick-up &amp; delivery available</p>

    <footer class="contact-bar">
      <span class="contact-bar__item"><svg width="13" height="13" viewBox="0 0 24 24"><path d="M6.6 10.8a15 15 0 0 0 6.6 6.6l2.2-2.2a1 1 0 0 1 1-.25 11.4 11.4 0 0 0 3.6.6 1 1 0 0 1 1 1V20a1 1 0 0 1-1 1A17 17 0 0 1 3 4a1 1 0 0 1 1-1h3.5a1 1 0 0 1 1 1 11.4 11.4 0 0 0 .6 3.6 1 1 0 0 1-.25 1z" fill="#fff"/></svg>920-555-0147</span>
      <span class="contact-bar__sep"></span>
      <span class="contact-bar__item"><svg width="12" height="12" viewBox="0 0 24 24"><g fill="none" stroke="#fff" stroke-width="2"><circle cx="12" cy="12" r="10"/><ellipse cx="12" cy="12" rx="4" ry="10"/><path d="M2 12h20"/></g></svg>www.birchhollowyardllc.example</span>
    </footer>
  </section>
  <p class="size-label size-label--quarter">1/4 page ad</p>

</div>
</body>
</html>
```